Flyer for Compassion training days

I need a A5-size, single-sided flyer design for my training days. They are weekends in a blend of Compassionate Communication and Buddhist teachings called Gentlewise Dialogue. The logo for Gentlewise that should be included.
The flyer needs room for 1) course title, 2) course dates, location & price, 3) course description, 4) booking info, 5) my picture & short bio, and 6) the gentlewise.co website (yes, it is 'co' and not 'com).
Updates

Target Market(s)

Women 35-65 years, well-educated, spiritually minded. May have interests like yoga and meditation.

Industry/Entity Type

Health And Wellness

Font styles to use
Sans Serif
Other font styles liked:
• Blue Plaque, Josefina are both great

Colors
fbf289
fdf9cf
cfeae6
33b8a4

Requirements
Must have
• The Gentlewise logo; my picture.
• Elegance. Calm and expansive feel.
• The poster provided in the project files shows you the kind of information I need to include.
• Colours -- greens and yellows, but the options on craft plaza are not quite the right shades.
• The logo colour can be changed.
Nice to have
• Classy (but not cliche) image associated with Buddhism; gentle curves similar to those on the business card (see project files).
Should not have
• Dark background. Busy, loud design. Overly 'swirly' design. Images that I have to buy separately.

```html
<!DOCTYPE html>
<html lang="en">
<head>
<meta charset="utf-8">
<title>Gentlewise Dialogue – Core Course Flyer</title>
<link href="https://fonts.googleapis.com/css2?family=Josefin+Sans:wght@300;400;600;700&display=swap" rel="stylesheet">
<style>
  :root {
    --teal: #1fa58e;
    --teal-light: #33b8a4;
    --mint: #cfeae6;
    --cream: #fdf9cf;
    --lemon: #fbf289;
    --ink: #2f2f2f;
    --ink-soft: #3d3d3d;
    --dark-pill: #2b2422;
    --paper: #f4f4f2;
    --stage: #e9ebe6;
  }
  * { box-sizing: border-box; margin: 0; padding: 0; }
  html, body { width: 1200px; height: 1199px; overflow: hidden; }
  body {
    background: var(--stage);
    font-family: "Josefin Sans", sans-serif;
    color: var(--ink);
    position: relative;
  }
  .flyer {
    position: absolute;
    left: 344px; top: 71px;
    width: 725px; height: 1028px;
    background: radial-gradient(ellipse at 60% 55%, #ffffff 0%, #f3f2ef 60%, #e9e8e4 100%);
    overflow: hidden;
  }
  .hero { position: absolute; left: 0; top: 0; width: 725px; height: 270px; }
  .headline {
    position: absolute; left: 0; top: 186px; width: 682px;
    text-align: center; font-size: 27px; line-height: 31px; font-weight: 400;
  }
  .headline .accent { color: var(--teal); }
  .title {
    position: absolute; left: 0; top: 254px; width: 745px;
    text-align: center; font-size: 62px; font-weight: 300; letter-spacing: 0.5px;
    color: var(--ink-soft);
  }
  .brand {
    position: absolute; left: 62px; top: 380px; width: 170px;
    display: flex; align-items: center; gap: 10px;
  }
  .brand-dot { width: 22px; height: 22px; border-radius: 50%; background: var(--teal-light); flex: none; }
  .brand-name { font-size: 28px; font-weight: 600; color: var(--teal); }
  .intro {
    position: absolute; left: 245px; top: 342px; width: 425px;
    font-size: 19px; line-height: 25px; font-weight: 400;
  }
  .explore-pill {
    position: absolute; left: 223px; top: 486px; width: 432px; height: 35px;
    background: var(--teal); color: #fff; border-radius: 8px 0 8px 0;
    font-size: 20px; line-height: 38px; padding-left: 36px;
  }
  .course-info { position: absolute; left: 64px; top: 524px; width: 160px; }
  .course-label { color: var(--teal); font-size: 24px; }
  .course-dates { font-size: 32px; font-weight: 600; margin-top: 4px; line-height: 36px; }
  .course-venue, .course-price { font-size: 18px; font-weight: 600; line-height: 23px; }
  .course-venue { margin-top: 6px; }
  .course-price { margin-top: 6px; }
  .website { position: absolute; left: 64px; top: 712px; font-size: 19px; font-weight: 600; }
  .explore-list { position: absolute; left: 246px; top: 530px; width: 430px; list-style: none; }
  .explore-list li {
    position: relative; padding-left: 24px; font-size: 16px; font-weight: 600;
    line-height: 21px; margin-bottom: 6px;
  }
  .explore-list svg { position: absolute; left: 0; top: 2px; }
  .audience {
    position: absolute; left: 245px; top: 676px; width: 430px;
    font-size: 17px; line-height: 22.5px;
  }
  .portrait { position: absolute; left: 0; top: 758px; width: 262px; height: 270px; }
  .booking-pill {
    position: absolute; left: 245px; top: 807px; width: 100px; height: 27px;
    background: var(--teal); color: #fff; border-radius: 8px 0 8px 0;
    font-size: 19px; font-weight: 600; text-align: center; line-height: 29px;
  }
  .booking-text {
    position: absolute; left: 365px; top: 799px; font-size: 18px; font-weight: 600; line-height: 23px;
  }
  .booking-text .email { color: var(--teal); }
  .facilitator-pill {
    position: absolute; left: 211px; top: 862px; width: 135px; height: 25px;
    background: var(--dark-pill); color: #fff; border-radius: 8px 0 8px 0;
    font-size: 17px; text-align: center; line-height: 27px;
  }
  .bio {
    position: absolute; left: 260px; top: 868px; width: 420px;
    font-size: 17px; line-height: 22.5px; text-indent: 98px;
  }
  .bio-coaching {
    position: absolute; left: 261px; top: 965px; font-size: 17px; font-weight: 600;
  }
</style>
</head>
<body>
  <article class="flyer">
    <svg class="hero" viewBox="0 0 725 270" role="img" aria-label="Photograph of an autumn park with golden trees in sunlight and a hand holding a yellow butterfly">
      <defs>
        <linearGradient id="park" x1="0" y1="0" x2="1" y2="0">
          <stop offset="0" stop-color="#c9761e"/>
          <stop offset="0.45" stop-color="#8a8a3a"/>
          <stop offset="0.8" stop-color="#e7d27a"/>
          <stop offset="1" stop-color="#f7edb5"/>
        </linearGradient>
        <linearGradient id="hand" x1="0" y1="0" x2="0" y2="1">
          <stop offset="0" stop-color="#f1c7a8"/>
          <stop offset="1" stop-color="#d99a76"/>
        </linearGradient>
      </defs>
      <path d="M0 0 H725 V130 C560 150 470 110 330 118 C200 125 90 150 0 95 Z" fill="url(#park)"/>
      <path d="M0 78 C90 140 200 118 330 108 C470 98 570 140 725 118 V150 C570 155 470 126 330 132 C200 140 90 165 0 110 Z" fill="var(--teal)"/>
      <path d="M520 110 C600 80 660 60 725 60 V95 C650 100 590 110 520 120 Z" fill="var(--lemon)" opacity="0.7"/>
      <path d="M520 150 C560 100 600 80 630 75 L725 140 V265 C640 250 560 210 520 150 Z" fill="url(#hand)"/>
    </svg>

    <h2 class="headline">Mindfulness + <span class="accent">Kindness</span> +<br>Compassionate Communication =</h2>
    <h1 class="title">Gentlewise Dialogue</h1>

    <div class="brand">
      <span class="brand-dot"></span>
      <span class="brand-name">Gentlewise</span>
    </div>

    <p class="intro">Gentlewise Dialogue can help you increase awareness &amp; compassion in everyday speech (with yourself &amp; others), better understand your own patterns, and build resilience to challenging situations. Choose from:</p>

    <div class="explore-pill">In this 2-day Core Course, we’ll explore:</div>

    <section class="course-info">
      <p class="course-label">Core Course</p>
      <p class="course-dates">11-12 Dec</p>
      <p class="course-venue">Larchfield Hall,<br>Edinburgh</p>
      <p class="course-price">£125/100</p>
    </section>
    <p class="website">www.gentlewise.co</p>

    <ul class="explore-list">
      <li><svg width="14" height="14" viewBox="0 0 14 14"><path d="M1 7 L5 11 L13 2" fill="none" stroke="var(--teal)" stroke-width="1.6"/></svg>Compassionate Communication;</li>
      <li><svg width="14" height="14" viewBox="0 0 14 14"><path d="M1 7 L5 11 L13 2" fill="none" stroke="var(--teal)" stroke-width="1.6"/></svg>Buddhist teachings on Right Speech, loving-kindness, Right Effort, and more;</li>
      <li><svg width="14" height="14" viewBox="0 0 14 14"><path d="M1 7 L5 11 L13 2" fill="none" stroke="var(--teal)" stroke-width="1.6"/></svg>mindfulness practices;</li>
      <li><svg width="14" height="14" viewBox="0 0 14 14"><path d="M1 7 L5 11 L13 2" fill="none" stroke="var(--teal)" stroke-width="1.6"/></svg>choices available to us in our everyday speech.</li>
    </ul>

    <p class="audience">This workshop will be of interest if you’d like to improve personal and/or professional relationships. Open to all, best suited to those with at least 1 year’s experience with Mindfulness, Buddhism, or Compassionate Communication / NVC.</p>

    <svg class="portrait" viewBox="0 0 262 270" role="img" aria-label="Sepia portrait photograph of the course facilitator">
      <defs>
        <radialGradient id="sepia" cx="0.45" cy="0.45" r="0.6">
          <stop offset="0" stop-color="#c9b29a"/>
          <stop offset="0.7" stop-color="#7d6553"/>
          <stop offset="1" stop-color="#e9e6e1" stop-opacity="0"/>
        </radialGradient>
      </defs>
      <path d="M0 270 V40 C40 0 140 -10 200 40 C230 90 230 160 262 270 Z" fill="url(#sepia)"/>
    </svg>

    <div class="booking-pill">booking</div>
    <p class="booking-text">Book online at TicketNook or<br>write <span class="email">maren@gentlewise.co</span></p>

    <div class="facilitator-pill">facilitator</div>
    <p class="bio">Maren Holloway is an experienced group facilitator, having worked with a range of organisations and presented at a number of festivals &amp; conferences.</p>
    <p class="bio-coaching">Maren offers coaching in Gentlewise Dialogue.</p>
  </article>
</body>
</html>
```